Irrigation Business needs their business cards modernised and revamped

I would like to keep my current logo, colours and revamp the format of the card.

I would like the card to be clean yet important.

Im not sure if you include texture but i would like the named logo to be indented into the card etc.

show me something alive and free something thats clinical to the point yet has a feel of achievement. i would like people to go nice card.

Target Market(s)

high end clients, corporate, sports field manger, the guys that make the decisions

Industry/Entity Type

Business

Contact Information for Business Card

nformation to be included

Dean Harlow (Director)
0487305526
dean@kolvat.biz
www.kestonfieldworks.com

instagram logo
google logo
facebook logo

Colors

Designer to choose colors to be used in the design.

Requirements
Nice to have
• indentations a really nice feel to the card good texture

```html
<!DOCTYPE html>
<html lang="en">
<head>
<meta charset="utf-8">
<title>Keston Fieldworks – Business Card</title>
<link rel="stylesheet" href="https://fonts.googleapis.com/css2?family=Oswald:wght@500&family=Montserrat:wght@400;700&display=swap">
<style>
  :root {
    --page-bg: #1a1a1a;
    --card-bg: #1f1f1f;
    --card-bg-light: #2c2c2c;
    --brand-blue: #2f73c4;
    --accent-cyan: #2aa8e0;
    --text-light: #f2f2f2;
    --emboss-grey: #4a4a4a;
    --social-grey: #5a5a5a;
  }
  * { margin: 0; padding: 0; box-sizing: border-box; }
  html, body {
    width: 1200px; height: 900px; overflow: hidden;
    background: var(--page-bg);
    font-family: "Montserrat", sans-serif;
  }
  .canvas {
    position: relative; width: 1200px; height: 900px;
  }
  .card {
    position: absolute; left: 285px; width: 630px; height: 360px;
    background: linear-gradient(135deg, var(--card-bg) 0%, var(--card-bg-light) 100%);
    box-shadow: 0 10px 30px rgba(0,0,0,0.45);
  }
  .card--front { top: 60px; }
  .card--back { top: 480px; }

  /* front */
  .brand {
    position: absolute; inset: 0;
    display: flex; flex-direction: column; align-items: center; justify-content: center; gap: 14px;
  }
  .brand__mark {
    width: 76px; height: 76px; border-radius: 50%;
    background: var(--emboss-grey);
  }
  .brand__name {
    font-family: "Montserrat", sans-serif; font-weight: 700;
    font-size: 30px; letter-spacing: 1px; color: var(--emboss-grey);
  }

  /* back */
  .identity {
    position: absolute; right: 385px; top: 118px; text-align: right;
  }
  .identity__name {
    font-family: "Oswald", sans-serif; font-weight: 500;
    font-size: 38px; line-height: 1; color: var(--brand-blue);
    text-transform: uppercase; letter-spacing: 0.5px;
  }
  .identity__role {
    margin-top: 8px; font-size: 18px; color: var(--text-light);
  }
  .divider {
    position: absolute; left: 265px; top: 112px; width: 2px; height: 74px;
    background: var(--accent-cyan);
  }
  .contacts {
    position: absolute; left: 290px; top: 116px; list-style: none;
  }
  .contacts__item {
    display: flex; align-items: center; gap: 14px;
    font-size: 17px; color: var(--text-light); height: 25px;
  }
  .contacts__icon { width: 16px; height: 16px; flex: none; }
  .socials {
    position: absolute; left: 228px; top: 282px; display: flex; gap: 10px;
  }
  .socials__badge {
    width: 22px; height: 22px; border-radius: 50%; background: var(--social-grey);
  }
</style>
</head>
<body>
<main class="canvas">
  <section class="card card--front" aria-label="Card front">
    <div class="brand">
      <span class="brand__mark" aria-hidden="true"></span>
      <span class="brand__name">KESTON FIELDWORKS</span>
    </div>
  </section>

  <section class="card card--back" aria-label="Card back">
    <div class="identity">
      <h1 class="identity__name">Dean Harlow</h1>
      <p class="identity__role">Director</p>
    </div>
    <span class="divider" aria-hidden="true"></span>
    <ul class="contacts">
      <li class="contacts__item">
        <svg class="contacts__icon" viewBox="0 0 16 16" aria-hidden="true"><path d="M4 1.5l2.2 3-1.3 1.6c.9 2 2.4 3.5 4.4 4.4l1.6-1.3 3 2.2-1.3 2.6C7 13.7 2.3 9 1.5 3.4z" fill="var(--accent-cyan)"/></svg>
        <span>0487305526</span>
      </li>
      <li class="contacts__item">
        <svg class="contacts__icon" viewBox="0 0 16 16" aria-hidden="true"><rect x="1" y="3" width="14" height="10" fill="var(--accent-cyan)"/><path d="M1 3l7 6 7-6" fill="none" stroke="var(--card-bg)" stroke-width="1.4"/></svg>
        <span>dean@kolvat.biz</span>
      </li>
      <li class="contacts__item">
        <svg class="contacts__icon" viewBox="0 0 16 16" aria-hidden="true"><g fill="none" stroke="var(--accent-cyan)" stroke-width="1.3"><circle cx="8" cy="8" r="6.5"/><ellipse cx="8" cy="8" rx="3" ry="6.5"/><path d="M1.5 8h13M2.5 4.8h11M2.5 11.2h11"/></g></svg>
        <span>www.kestonfieldworks.com</span>
      </li>
    </ul>
    <div class="socials" aria-label="Social channels">
      <span class="socials__badge"></span>
      <span class="socials__badge"></span>
      <span class="socials__badge"></span>
    </div>
  </section>
</main>
</body>
</html>
```